Local fast-growing company in the service sector

We are looking for a modern business card design, which should also appear on our letterheads

Target Market(s)

Private and industrial sectors

Contact Information for Business Card

Vorname Name
Kellberger Str. 18
74389 Lindenhof
Tel.: 07146-839214-0
Name@agentur-kvtl.de

Colors
9d9d9d
919191
aaaaaa

Requirements
Must have
• The logo (file) in silver

```html
<!DOCTYPE html>
<html lang="de">
<head>
<meta charset="utf-8">
<title>KVTL Visitenkarte</title>
<link rel="stylesheet" href="https://fonts.googleapis.com/css2?family=Lato:wght@300;400;700&display=swap">
<style>
  :root {
    --page: #e6e6e6;
    --card: #fbfbfb;
    --silver: #9d9d9d;
    --silver-mid: #919191;
    --silver-light: #aaaaaa;
    --band-dark: #58595b;
    --text-dark: #4a4a4a;
    --text-soft: #8a8a8a;
    --rule: #b9b9b9;
  }
  * { margin: 0; padding: 0; box-sizing: border-box; }
  html, body { width: 1200px; height: 900px; overflow: hidden; }
  body {
    background: var(--page);
    font-family: "Lato", Arial, sans-serif;
    display: flex; flex-direction: column; align-items: center; justify-content: center;
    gap: 40px;
  }
  .card {
    position: relative;
    width: 680px; height: 390px;
    background: var(--card);
    box-shadow: 0 6px 18px rgba(0,0,0,.12);
    overflow: hidden;
  }
  .wordmark {
    position: absolute;
    display: flex; align-items: center; gap: 14px;
    color: var(--silver);
    font-weight: 700;
    letter-spacing: 2px;
    white-space: nowrap;
  }
  .wordmark .mark-square { background: var(--silver-light); }
  .card-front .wordmark { left: 50%; top: 50%; transform: translate(-50%, -50%); font-size: 84px; }
  .card-front .mark-square { width: 58px; height: 58px; }
  .card-back .wordmark { right: 60px; top: 40px; font-size: 46px; }
  .card-back .mark-square { width: 32px; height: 32px; }
  .rule { position: absolute; height: 1px; background: var(--rule); }
  .rule-top { left: 330px; right: 60px; top: 140px; }
  .rule-name { left: 60px; width: 430px; top: 268px; }
  .address {
    position: absolute; right: 60px; top: 160px;
    text-align: right; color: var(--text-soft);
    font-size: 17px; line-height: 24px; font-weight: 400;
    white-space: nowrap;
  }
  .person {
    position: absolute; left: 60px; top: 236px;
    color: var(--text-dark); font-size: 20px; font-weight: 400;
    text-transform: uppercase; letter-spacing: -.3px;
    white-space: nowrap;
  }
  .contact { position: absolute; left: 60px; top: 282px; list-style: none; color: var(--text-soft); font-size: 16px; line-height: 24px; }
  .contact li { display: flex; align-items: center; gap: 10px; white-space: nowrap; }
  .contact svg { width: 13px; height: 13px; fill: var(--text-dark); }
  .band { position: absolute; left: 0; bottom: 0; width: 680px; height: 60px; }
  .web {
    position: absolute; right: 60px; bottom: 12px;
    color: #fff; font-size: 17px; letter-spacing: 2px;
    white-space: nowrap;
  }
</style>
</head>
<body>
  <section class="card card-front">
    <div class="wordmark"><span class="mark-square"></span><span>KVTL</span></div>
  </section>

  <section class="card card-back">
    <div class="wordmark"><span class="mark-square"></span><span>KVTL</span></div>
    <div class="rule rule-top"></div>
    <p class="address">Kellberger Str. 18<br>74389 Lindenhof</p>
    <p class="person">Laura Becker</p>
    <div class="rule rule-name"></div>
    <ul class="contact">
      <li><svg viewBox="0 0 16 16"><path d="M3.6 1.2l2.4 2.6-1.3 1.9c.9 2 2.5 3.6 4.6 4.6l1.9-1.3 2.6 2.4-1.4 2.4C7.4 14 2 8.6 1.2 3z"/></svg>07146-839214-0</li>
      <li><svg viewBox="0 0 16 16"><path d="M1 3h14v10H1zM2.5 4.5v.3L8 9l5.5-4.2v-.3zM2.5 6.6v5h11v-5L8 10.8z"/></svg>laura@agentur-kvtl.de</li>
    </ul>
    <svg class="band" viewBox="0 0 680 60" aria-hidden="true">
      <path d="M0 28 H500 L520 6 H680 V16 H524 L504 38 H0 Z" fill="var(--silver-light)"/>
      <path d="M0 38 H504 L524 16 H680 V60 H0 Z" fill="var(--band-dark)"/>
    </svg>
    <span class="web">agentur-kvtl.de</span>
  </section>
</body>
</html>
```